OBK Farcoast Logistics Limited

We need the buissnes card to be very exclusive. As we are all young in our company. We need this to be the gate to make our clients feel deep interest for us.

We are focused in as International Trade advisors, and our products go from Oil Tanker Ships to Rubber balls for dogs.

Our Slogan is Bringing Distant Near.
And our main marketing will be through Internet.

We were stablished in 2009 In Mexico and we also have offices in Hong Kong.
We have representatives in China and Europe.

Target Market(s)

Is every company or Individual that wants to develop an International Project or product development or Logistic service of Goods and people.
Some of our current projects are Ship Brokerage, Mine Brokerage, Real State and Product Pormotional development.

Industry/Entity Type

It Company

Requirements
Must have
• Our Logo and slogan, and make the card accoriding to the logo.
Nice to have
• Our Colors

```html
<!DOCTYPE html>
<html lang="en">
<head>
<meta charset="utf-8">
<title>Business Card – Front and Back</title>
<link rel="stylesheet" href="https://fonts.googleapis.com/css2?family=Open+Sans:wght@300;400;600;700&display=swap">
<style>
  :root {
    --stage: #ececec;
    --card: #ffffff;
    --brand-blue: #1b7db4;
    --brand-sky: #2f9fd6;
    --brand-green: #8cc63f;
    --ink: #222222;
    --ink-soft: #333333;
  }
  * { margin: 0; padding: 0; box-sizing: border-box; }
  html, body {
    width: 1200px;
    height: 989px;
    overflow: hidden;
  }
  body {
    background: var(--stage);
    font-family: "Open Sans", Arial, sans-serif;
    color: var(--ink);
    position: relative;
  }
  .card {
    position: absolute;
    top: 59px;
    width: 494px;
    height: 864px;
    background: var(--card);
    box-shadow: 0 2px 6px rgba(0,0,0,0.18);
  }
  .card--front { left: 66px; }
  .card--back { left: 616px; }

  .brand-mark {
    position: absolute;
    left: 50%;
    transform: translateX(-50%);
    border-radius: 50%;
    background: var(--brand-sky);
  }
  .card--front .brand-mark { top: 45px; width: 280px; height: 280px; }
  .card--back .brand-mark { top: 250px; width: 280px; height: 280px; }

  .brand-name {
    position: absolute;
    left: 0;
    width: 100%;
    text-align: center;
    font-weight: 300;
    color: var(--brand-green);
    line-height: 1;
    letter-spacing: 6px;
  }
  .card--front .brand-name { top: 334px; font-size: 100px; }
  .card--back .brand-name { top: 556px; font-size: 64px; }

  .slogan {
    position: absolute;
    top: 440px;
    left: 0;
    width: 100%;
    text-align: center;
    font-size: 19px;
    color: var(--brand-sky);
  }

  .rule {
    position: absolute;
    left: 0;
    width: 100%;
    height: 3px;
    background: var(--brand-green);
  }
  .rule--top { top: 522px; }
  .rule--bottom { top: 627px; }

  .name-band {
    position: absolute;
    top: 536px;
    left: 0;
    width: 100%;
    height: 80px;
    background: var(--brand-blue);
    color: #fff;
    display: flex;
    align-items: center;
    justify-content: center;
    font-size: 20px;
  }
  .name-band .person { font-weight: 700; font-size: 25px; }

  .contact {
    position: absolute;
    left: 0;
    width: 100%;
    display: flex;
    align-items: center;
    justify-content: center;
    gap: 8px;
    font-size: 21px;
    color: var(--ink-soft);
  }
  .contact svg { width: 20px; height: 20px; fill: var(--brand-blue); flex: none; }
  .contact .gap { width: 14px; }
  .contact--phones { top: 682px; }
  .contact--email { top: 732px; }
  .contact--address { top: 796px; letter-spacing: 0.5px; }

  .website {
    position: absolute;
    bottom: 44px;
    left: 0;
    width: 100%;
    text-align: center;
    font-size: 22px;
    letter-spacing: 4px;
    color: var(--ink-soft);
  }
  .website .domain { color: var(--brand-blue); }
</style>
</head>
<body>
  <section class="card card--front" aria-label="Business card front">
    <div class="brand-mark" aria-hidden="true"></div>
    <div class="brand-name">OBK</div>
    <p class="slogan">Bringing Distant Near</p>

    <div class="rule rule--top"></div>
    <div class="name-band"><span class="person">Your Name,</span>&nbsp;Position</div>
    <div class="rule rule--bottom"></div>

    <p class="contact contact--phones">
      <svg viewBox="0 0 20 20" aria-hidden="true"><circle cx="10" cy="10" r="9.5" fill="none" stroke="#1b7db4" stroke-width="1.5"/><path d="M6.5 5.5c.6-.6 1.3-.5 1.7.1l1 1.5c.3.5.2 1-.2 1.4l-.6.5c.5 1.1 1.3 1.9 2.4 2.5l.5-.6c.4-.4.9-.5 1.4-.2l1.5 1c.6.4.7 1.1.1 1.7l-.7.7c-2.8.8-7.8-4.2-7.8-7.3z"/></svg>
      123-456-7890
      <span class="gap"></span>
      <svg viewBox="0 0 20 20" aria-hidden="true"><rect x="5" y="1" width="10" height="18" rx="2"/><rect x="7" y="4" width="6" height="6" fill="#fff"/><rect x="7" y="12" width="6" height="4" fill="#fff" opacity=".6"/></svg>
      123-456-7890
    </p>
    <p class="contact contact--email">
      <svg viewBox="0 0 20 20" aria-hidden="true"><circle cx="10" cy="10" r="10"/><rect x="4.5" y="6.5" width="11" height="7.5" fill="#fff"/><path d="M4.5 6.5l5.5 4.2 5.5-4.2" fill="none" stroke="#1b7db4" stroke-width="1.2"/></svg>
      info@obkfarcoast.com
    </p>
    <p class="contact contact--address">00, Complex Name, City, State, 00045</p>
  </section>

  <section class="card card--back" aria-label="Business card back">
    <div class="brand-mark" aria-hidden="true"></div>
    <div class="brand-name">OBK</div>
    <p class="website">www.<span class="domain">obkfarcoast</span>.com</p>
  </section>
</body>
</html>
```